Velmor Spire Nine Flash website

we need a website to cater to 2 aspect of the business. We have Velmor spire residence and velmor spire office. For the office, we will get their inquire and arrange a face to face meetup to show them the office area for rent. For the residence side, it will need to be like staylane or roomvio.com. we want to allow them to book online for the date they need. We have a total of 10 different room configurations starting at $70 per night and up depending on the size of the room. example of the design is https://brisquelodge.com/

Target Market(s)

the website should have detail information on the layout, designs, and luxury of the building.

Industry/Entity Type

office and service appartment rental/lease

Coding

Coded - Design and coding required

Number of Pages Required

5+ page

Requirements
Must have
• a luxury perspective
Nice to have
• example https://brisquelodge.com/

```html
<!DOCTYPE html>
<html lang="en">
<head>
<meta charset="utf-8">
<title>Velmor Spire Nine — Find your Dream Residence</title>
<link href="https://fonts.googleapis.com/css2?family=DM+Sans:wght@400;500;700&display=swap" rel="stylesheet">
<style>
:root{
  --cream:#fdf6e9;
  --ink:#1c1712;
  --brown:#5c4416;
  --olive:#7b5a1c;
  --maroon:#4b0b2d;
  --plum:#5a0f3c;
  --footer:#3b0a24;
  --line:#9a948c;
  --white:#ffffff;
}
*{margin:0;padding:0;box-sizing:border-box}
html,body{width:1200px;height:4637px;overflow:hidden}
body{background:var(--cream);font-family:"DM Sans",sans-serif;color:var(--ink);position:relative}
.abs{position:absolute}
.photo{position:absolute}

/* hero */
.hero{left:0;top:0;width:1200px;height:801px;background:linear-gradient(180deg,#3a3f36 0%,#2b2a24 35%,#3b2e1d 60%,#2e3a1e 85%,#24301a 100%);overflow:hidden}
.hero-glow{left:560px;top:300px;width:520px;height:300px;background:radial-gradient(ellipse at center,rgba(214,150,70,.55),rgba(214,150,70,0) 70%)}
.brand-top{left:78px;top:22px;color:var(--white);font-size:13px;display:flex;flex-direction:column;align-items:center;gap:6px}
.brand-top .mark{width:22px;height:22px;border:1.5px solid var(--white)}
.nav{right:90px;top:30px;display:flex;gap:24px;font-size:15px;color:#d8d2c8}
.nav .active{color:var(--white);font-weight:700}
.hero-title{left:104px;top:232px;font-size:72px;line-height:100px;font-weight:700;color:var(--white)}
.btn{display:inline-block;background:var(--maroon);color:var(--white);font-size:20px;text-decoration:none}
.hero-btn{position:absolute;left:112px;top:477px;width:171px;height:50px;line-height:50px;text-align:center}
.search{left:79px;top:738px;width:1035px;height:63px;background:rgba(28,26,24,.72);display:flex;align-items:center;color:#d9d4cc;font-size:16px}
.search .field{display:flex;align-items:center;gap:14px;padding-left:14px;border-right:3px solid #e8e2d8;height:50px}
.search .f1{width:349px}.search .f2{width:214px;padding-left:46px}.search .f3{width:225px;padding-left:46px}.search .f4{width:180px;padding-left:46px;border-right:none}
.search .go{position:absolute;right:0;top:0;width:67px;height:63px;background:var(--plum);display:flex;align-items:center;justify-content:center}

/* offer */
.offer-title{left:79px;top:894px;font-size:40px;font-weight:700}
.offer-sub{left:79px;top:948px;font-size:32px;line-height:46px;width:460px}
.offer-text{left:79px;top:1080px;width:420px;font-size:23px;line-height:32.5px}
.offer-photo{left:702px;top:869px;width:399px;height:550px;background:linear-gradient(160deg,#5b7a5a 0%,#1d2126 40%,#2a2d33 60%,#b5773e 85%,#6a5a44 100%)}

/* services */
.section-title{width:1200px;left:0;text-align:center;font-size:40px;font-weight:500}
.services{left:54px;top:1551px;display:flex;gap:54px}
.card{width:328px;height:422px;background:var(--brown);color:var(--white);text-align:center;padding-top:46px}
.card svg{display:block;margin:0 auto}
.card h3{font-size:34px;font-weight:400;margin-top:14px}
.card p{font-size:23px;line-height:33px;margin:28px auto 0;width:220px}

/* layout */
.layout-title{right:124px;top:2030px;font-size:40px;font-weight:700}
.layout-text{left:568px;top:2085px;width:550px;font-size:26px;line-height:36px}
.plan{left:81px;top:2087px;width:416px;height:428px;background:linear-gradient(135deg,#8f8774,#7a7360);box-shadow:22px 26px 40px rgba(60,45,20,.25)}
.filters{left:568px;top:2396px;display:flex;gap:29px}
.filter{width:104px;text-align:center;color:var(--brown);font-size:19px;white-space:nowrap;display:flex;flex-direction:column;align-items:center}
.filter .ring{width:104px;height:104px;border-radius:50%;background:var(--white);box-shadow:0 4px 10px rgba(0,0,0,.18);display:flex;align-items:center;justify-content:center;margin-bottom:14px}

/* gallery */
.gallery-main{left:79px;top:2763px;width:1031px;height:455px;background:linear-gradient(180deg,#3c63a8 0%,#7fa0c8 30%,#6c7c55 55%,#3f6a2a 80%,#5f8f34 100%)}
.dots{display:flex;gap:14px}
.dots span{width:90px;height:4px;background:var(--line)}
.dots .on{background:var(--brown)}
.interior-title{left:0;width:1166px;text-align:center;top:3260px;font-size:34px;font-weight:400}
.int1{left:22px;top:3321px;width:365px;height:353px;background:linear-gradient(160deg,#b77a34 0%,#d9c8a8 40%,#9d8a70 75%,#6a4a2e 100%)}
.int2{left:410px;top:3321px;width:376px;height:353px;background:linear-gradient(180deg,#2b241f 0%,#5a4334 40%,#3a3330 70%,#7c7772 100%)}
.int3{left:810px;top:3321px;width:314px;height:353px;background:linear-gradient(180deg,#3b2a22 0%,#7a4a2a 40%,#4b3329 75%,#9a8c84 100%)}

/* cta */
.cta{left:0;top:3776px;width:1200px;height:488px;background:var(--olive);color:var(--white)}
.cta h2{position:absolute;left:81px;top:58px;font-size:40px;font-weight:500}
.cta p{position:absolute;left:81px;top:138px;width:470px;font-size:23px;line-height:32.5px}
.cta .btn{position:absolute;left:81px;top:380px;width:144px;height:40px;line-height:40px;text-align:center;font-size:19px}
.cta-photo{left:754px;top:50px;width:333px;height:387px;background:linear-gradient(160deg,#6b4a33 0%,#3e2c22 40%,#d8d6d2 65%,#1c1a19 100%)}

/* footer */
.footer{left:0;top:4332px;width:1200px;height:305px;background:var(--footer);color:var(--white)}
.foot-brand{position:absolute;left:96px;top:44px;width:240px;text-align:center}
.foot-brand .mark{width:60px;height:60px;border:2px solid #c9b9c2;margin:0 auto 26px}
.foot-brand .name{font-size:26px;color:#e6dde2}
.socials{position:absolute;left:116px;top:202px;display:flex;gap:38px}
.socials span{width:28px;height:28px;border-radius:50%;border:2.5px solid var(--white)}
.fcol{position:absolute;top:76px;font-size:16px;line-height:35px}
.fcol h4{font-size:20px;font-weight:700;margin-bottom:6px}
.copy{position:absolute;left:0;width:1200px;text-align:center;top:264px;font-size:16px;color:#9c7d8d}
</style>
</head>
<body>

<header class="abs hero" role="img" aria-label="Photograph of a modern timber-clad house lit at dusk among tall trees">
  <div class="abs hero-glow"></div>
</header>
<div class="abs brand-top"><span class="mark"></span>Velmor Spire Nine</div>
<nav class="abs nav">
  <span class="active">Home</span><span>Residence</span><span>Location</span><span>Office</span><span>About us</span><span>Register Now</span>
</nav>
<h1 class="abs hero-title">Find your Dream<br>Residence</h1>
<a class="btn hero-btn">Learn More</a>

<form class="abs search">
  <div class="field f1">
    <svg width="34" height="30" viewBox="0 0 34 30" fill="none" stroke="#fff" stroke-width="2"><path d="M2 5l9-3 12 4 9-3v22l-9 3-12-4-9 3z M11 2v22 M23 6v22"/></svg>
    Write your destination property
  </div>
  <div class="field f2">
    <svg width="34" height="34" viewBox="0 0 34 34" fill="none" stroke="#fff" stroke-width="2"><rect x="3" y="6" width="28" height="25" rx="4"/><path d="M3 13h28 M10 3v6 M24 3v6 M10 20h14 M10 25h8"/></svg>
    Check-in
  </div>
  <div class="field f3">
    <svg width="34" height="34" viewBox="0 0 34 34" fill="none" stroke="#fff" stroke-width="2"><rect x="3" y="6" width="28" height="25" rx="4"/><path d="M3 13h28 M10 3v6 M24 3v6 M10 20h14 M10 25h8"/></svg>
    Check-out
  </div>
  <div class="field f4">
    <svg width="32" height="34" viewBox="0 0 32 34" fill="none" stroke="#fff" stroke-width="2"><rect x="3" y="3" width="26" height="28" rx="2"/><path d="M9 10h4 M19 10h4 M9 17h4 M19 17h4 M9 24h4 M19 24h4"/></svg>
    Type
  </div>
  <span class="go"><svg width="38" height="38" viewBox="0 0 38 38" fill="none" stroke="#fff" stroke-width="2.5"><circle cx="20" cy="17" r="12"/><path d="M11 26l-8 9"/></svg></span>
</form>

<h2 class="abs offer-title">What We Offer</h2>
<p class="abs offer-sub">Smart features &amp; Modern Architecture</p>
<p class="abs offer-text">Discover a home-like experience in a place that is comfortable, safe, and quiet to live in. Featuring a modern design concept, your home will never feel outdated. Supported with the latest technology features, your daily activities will be assisted by our intelligent device system.</p>
<div class="photo offer-photo" role="img" aria-label="Photograph of a dark modern residence facade with wooden slats at dusk"></div>

<h2 class="abs section-title" style="top:1474px">Our Services</h2>
<section class="abs services">
  <article class="card">
    <svg width="42" height="46" viewBox="0 0 42 46" fill="none" stroke="#fff" stroke-width="2"><rect x="4" y="3" width="34" height="40" rx="3"/><path d="M12 13h5 M25 13h5 M12 22h5 M25 22h5 M12 31h5 M25 31h5"/></svg>
    <h3>Rent a Office</h3>
    <p>Renting a office provides flexibility and convenience, and we are here to assist you finding rental property</p>
  </article>
  <article class="card">
    <svg width="42" height="46" viewBox="0 0 42 46" fill="none" stroke="#fff" stroke-width="2"><path d="M4 20L21 4l17 16v23H4z M14 43V26h14v17"/></svg>
    <h3>Sell a Home</h3>
    <p>Selling your home provides flexibility and convenience, and we are here to help you find a suitable buyer</p>
  </article>
  <article class="card">
    <svg width="42" height="46" viewBox="0 0 42 46" fill="none" stroke="#fff" stroke-width="2"><path d="M4 20L21 4l17 16v23H4z M14 43V32h14v11"/><circle cx="16" cy="22" r="3"/><circle cx="26" cy="22" r="3"/></svg>
    <h3>Rent a Home</h3>
    <p>Renting a home provides flexibility and convenience, and we are here to assist you finding rental property</p>
  </article>
</section>

<div class="photo plan" role="img" aria-label="Architectural floor plan of the house showing bedrooms, living and dining areas"></div>
<h2 class="abs layout-title">House Layout</h2>
<p class="abs layout-text">find out more information about the house you want to rent. By viewing the floor plans displayed, you will find it easier to compare one house with another.</p>
<div class="abs filters">
  <div class="filter"><div class="ring"><svg width="56" height="56" viewBox="0 0 56 56" fill="none" stroke="#5c4416" stroke-width="3"><rect x="4" y="4" width="48" height="48"/><path d="M4 26h20V4 M24 36h28 M36 36v16 M14 26v26"/></svg></div>By type</div>
  <div class="filter"><div class="ring"><svg width="50" height="54" viewBox="0 0 50 54" fill="none" stroke="#5c4416" stroke-width="3"><rect x="4" y="4" width="42" height="46" rx="3"/><path d="M13 15h7 M30 15h7 M13 27h7 M30 27h7 M13 39h7 M30 39h7"/></svg></div>By unit</div>
  <div class="filter"><div class="ring"><svg width="56" height="44" viewBox="0 0 56 44" fill="none" stroke="#5c4416" stroke-width="3"><path d="M8 20V8a4 4 0 0 1 4-4h32a4 4 0 0 1 4 4v12 M4 36V24a4 4 0 0 1 4-4h40a4 4 0 0 1 4 4v12z M4 36v6 M52 36v6"/></svg></div>By bed</div>
  <div class="filter"><div class="ring"><svg width="48" height="52" viewBox="0 0 48 52" fill="none" stroke="#5c4416" stroke-width="3"><rect x="12" y="4" width="30" height="38" rx="3"/><rect x="4" y="12" width="30" height="36" rx="3" fill="#fff"/><path d="M12 24h14 M12 32h14"/></svg></div>By category</div>
</div>

<h2 class="abs section-title" style="top:2666px">Our Gallery</h2>
<div class="photo gallery-main" role="img" aria-label="Photograph of a modern apartment building surrounded by gardens and trees"></div>
<div class="abs dots" style="left:437px;top:3236px"><span></span><span></span><span></span><span class="on"></span></div>

<h3 class="abs interior-title">Interior of our residence</h3>
<div class="photo int1" role="img" aria-label="Photograph of a bright living room with armchairs and a fireplace"></div>
<div class="photo int2" role="img" aria-label="Photograph of a dark dining area with pendant lamps"></div>
<div class="photo int3" role="img" aria-label="Photograph of a restaurant space with a stone wall and warm lights"></div>
<div class="abs dots" style="left:399px;top:3709px"><span class="on"></span><span></span><span></span><span></span></div>

<section class="abs cta">
  <h2>Need an office rental? Let’s talk</h2>
  <p>we will find the right type of office for your company or team. With the facilities we provide, your company will experience the best office services from us. For further availability, you can contact us via chatlyne contact.</p>
  <a class="btn">Contact us</a>
  <div class="photo cta-photo" role="img" aria-label="Photograph of a laptop on a wooden desk beside a white chair"></div>
</section>

<footer class="abs footer">
  <div class="foot-brand"><div class="mark"></div><div class="name">Velmor Spire Nine</div></div>
  <div class="socials" aria-label="Social media links"><span></span><span></span><span></span><span></span></div>
  <div class="fcol" style="left:453px"><h4>Explore</h4>Location<br>Blog</div>
  <div class="fcol" style="left:642px"><h4>Services</h4>Residence<br>Office<br>Sell a house</div>
  <div class="fcol" style="left:862px"><h4>Contact Us</h4>+1 4120 5561 708<br>info@velmorspire.com</div>
  <div class="copy">VelmorSpireNine&nbsp; copyright 2024</div>
</footer>

</body>
</html>
```